Animal Eye Clinic needs a Business card

We are a new veterinary ophthalmology practice (Ridgeline Pet Vision Care) and we need a business card designed. We only see animal eyes - we are not a regular veterinary clinic. We already have a logo. We are looking for a professional, good looking business card to hand out to our clients. We are looking for something simple but professional and contemporary. Our logo is likely the only picture/graphic that needs to be on the card.
Updates

Contact Information for Business Card

Delia Vossman, BSc, DVM, MSc, DipACVO
Veterinary Ophthalmologist

Phone: 250.418.3927
Email: ridgelinepetvisioncare@mailbox-example.net
Website: ridgelinepetvisioncare-example.net
Address: 1874 Thornbury Rd
Kelowna, BC, V1X 4M9

Colors

Designer to choose colors to be used in the design.

Requirements
Must have
• Our logo (attached)

```html
<!DOCTYPE html>
<html lang="en">
<head>
<meta charset="utf-8">
<title>Ridgeline Pet Vision Care – Business Card</title>
<link rel="stylesheet" href="https://fonts.googleapis.com/css2?family=Archivo:wght@700;800&family=Roboto+Condensed:ital,wght@0,400;0,700;1,400;1,700&display=swap">
<style>
  :root{
    --bg:#2a2a2c;
    --card:#19191b;
    --teal:#1b9aab;
    --grey:#8a8a8d;
    --white:#ffffff;
  }
  *{box-sizing:border-box;margin:0;padding:0}
  html,body{width:1200px;height:900px;overflow:hidden}
  body{background:var(--bg);position:relative;font-family:"Roboto Condensed",sans-serif}
  .card{position:absolute;left:260px;width:680px;height:388px;background:var(--card);overflow:hidden}
  .card--front{top:50px}
  .card--back{top:462px}

  .brand{position:absolute;left:0;right:0;top:0;bottom:0;display:flex;align-items:center;justify-content:center;gap:18px}
  .brand__dot{width:44px;height:44px;border-radius:50%;background:var(--teal);flex:none}
  .brand__name{font-family:"Archivo",sans-serif;font-weight:800;font-size:30px;letter-spacing:1px;color:var(--teal);text-transform:uppercase}

  .person{position:absolute;left:36px;top:120px;width:262px;text-align:right}
  .person__name{font-family:"Archivo",sans-serif;font-weight:800;font-size:30px;color:var(--teal);letter-spacing:1px;line-height:1.05}
  .person__creds{font-weight:700;font-style:italic;font-size:19px;color:var(--teal);margin-top:4px}
  .person__title{font-style:italic;font-size:20px;color:var(--grey);margin-top:2px}

  .divider{position:absolute;left:316px;top:118px;width:2px;height:118px;background:var(--teal)}

  .contacts{position:absolute;left:334px;top:128px;list-style:none}
  .contacts li{display:flex;align-items:center;gap:9px;font-size:16px;color:var(--grey);height:32px}
  .contacts svg{width:18px;height:18px;flex:none}

  .address-band{position:absolute;left:0;right:0;bottom:0;height:80px;background:var(--teal);display:flex;align-items:center;justify-content:center}
  .address{color:var(--white);font-size:22px}
</style>
</head>
<body>
  <section class="card card--front">
    <div class="brand">
      <span class="brand__dot"></span>
      <span class="brand__name">Ridgeline Pet Vision Care</span>
    </div>
  </section>

  <section class="card card--back">
    <div class="person">
      <h1 class="person__name">DELIA VOSSMAN</h1>
      <p class="person__creds">BSc, DVM, MSc, DipACVO</p>
      <p class="person__title">Veterinary Ophthalmologist</p>
    </div>
    <div class="divider"></div>
    <ul class="contacts">
      <li>
        <svg viewBox="0 0 24 24" fill="none" stroke="#1b9aab" stroke-width="1.8"><circle cx="12" cy="12" r="10"/><path d="M8.5 7.5c.8-.8 1.6-.5 2 .3l.8 1.4c.3.6.1 1.1-.4 1.5l-.6.5c.6 1.4 1.6 2.4 3 3l.5-.6c.4-.5.9-.7 1.5-.4l1.4.8c.8.4 1.1 1.2.3 2-1.5 1.5-4.2.8-6.6-1.6S7 9 8.5 7.5z"/></svg>
        <span>250.418.3927</span>
      </li>
      <li>
        <svg viewBox="0 0 24 24" fill="none" stroke="#1b9aab" stroke-width="1.8"><rect x="2" y="5" width="20" height="14"/><path d="M2 5l10 8 10-8"/></svg>
        <span>ridgelinepetvisioncare@mailbox-example.net</span>
      </li>
      <li>
        <svg viewBox="0 0 24 24" fill="none" stroke="#1b9aab" stroke-width="1.8"><circle cx="12" cy="12" r="10"/><ellipse cx="12" cy="12" rx="4.5" ry="10"/><path d="M2 12h20M4 7h16M4 17h16"/></svg>
        <span>www.ridgelinepetvisioncare-example.net</span>
      </li>
    </ul>
    <div class="address-band">
      <p class="address">1874 Thornbury Rd, Kelowna, BC, V1X 4M9</p>
    </div>
  </section>
</body>
</html>
```